Marlow Estate Fixers (Handyman / Home Improvement Company)

Looking for a double sided professional looking business card with Logo attached to be highlighted on one side and throwing in an image of a handyman as an option would be nice to see as well. We are a company focused on providing quality Handyman and Home improvement services in a timely manner that is done right the first time with integrity

Industry/Entity Type

Handyman / Home Improvement

Contact Information for Business Card

(LOGO, Name, Mobile and office phone numbers, email) on front side of card, (the words "The SOLUTION to all of your Handyman and Home Improvement needs" followed by "Family Owned and Operated" at the very bottom) on the back.

Colors
EB3D1F
EC4F4E
F09395
F8D3D4
FCEDEE

Requirements
Must have
• Red, Gray, Black Color scheme
Should not have
• No Yellow or Blue colors

```html
<!DOCTYPE html>
<html lang="en">
<head>
<meta charset="utf-8">
<title>Marlow Estate Fixers – Business Card</title>
<link href="https://fonts.googleapis.com/css2?family=Poppins:wght@400;500;600&display=swap" rel="stylesheet">
<style>
  :root{
    --brand-red:#ec2a2f;
    --ink:#151515;
    --paper:#ffffff;
    --backdrop:#f1f1f1;
  }
  *{box-sizing:border-box;margin:0;padding:0}
  html,body{width:1200px;height:990px;overflow:hidden}
  body{background:var(--backdrop);font-family:"Poppins",sans-serif;position:relative}

  .card{position:absolute;left:244px;width:712px;height:407px;overflow:hidden}
  .card--back{top:68px;background:var(--brand-red);color:var(--paper)}
  .card--front{top:516px;background:var(--paper)}

  /* back side */
  .brand-lockup{position:absolute;left:0;right:0;top:130px;display:flex;align-items:center;justify-content:center;gap:14px}
  .brand-lockup__dot{width:40px;height:40px;border-radius:50%;background:var(--paper)}
  .brand-lockup__name{font-weight:600;font-size:34px;letter-spacing:.5px;color:var(--paper)}
  .tagline{position:absolute;left:0;right:0;text-align:center;font-size:17px;letter-spacing:.5px;line-height:22px}
  .tagline--family{top:336px}
  .tagline--services{top:358px}

  /* front side */
  .edge-bar{position:absolute;top:101px;width:16px;height:203px;background:var(--brand-red)}
  .edge-bar--left{left:0}
  .edge-bar--right{right:0}
  .front-brand{position:absolute;left:27px;top:112px;width:265px;height:181px;display:flex;flex-direction:column;align-items:center;justify-content:center;gap:12px}
  .front-brand__dot{width:46px;height:46px;border-radius:50%;background:var(--ink)}
  .front-brand__name{font-weight:600;font-size:26px;line-height:31px;text-align:center;color:var(--brand-red)}
  .divider{position:absolute;left:356px;top:81px;width:1px;height:244px;background:var(--brand-red)}

  .person{position:absolute;left:413px;top:110px;width:270px}
  .person__name{font-size:38px;line-height:42px;color:var(--brand-red);font-weight:400;white-space:nowrap}
  .person__name strong{font-weight:600}
  .person__title{font-size:18px;font-weight:500;color:var(--ink);margin-top:2px}

  .contact-list{position:absolute;left:410px;top:193px;list-style:none}
  .contact-list li{display:flex;align-items:center;gap:10px;height:24.5px;font-size:18px;color:var(--ink);white-space:nowrap}
  .contact-list svg{width:16px;height:16px;flex:none}
  .contact-list .accent{color:var(--brand-red)}

  .address{position:absolute;left:0;right:0;top:346px;text-align:center;font-size:19px;letter-spacing:.5px;color:var(--brand-red)}
</style>
</head>
<body>

<section class="card card--back" aria-label="Card back">
  <div class="brand-lockup">
    <span class="brand-lockup__dot"></span>
    <span class="brand-lockup__name">Marlow Estate Fixers</span>
  </div>
  <p class="tagline tagline--family">Family Owned and Operated</p>
  <p class="tagline tagline--services">Your SOLUTION to all of your Handyman and Home Improvement needs</p>
</section>

<section class="card card--front" aria-label="Card front">
  <span class="edge-bar edge-bar--left"></span>
  <span class="edge-bar edge-bar--right"></span>

  <div class="front-brand">
    <span class="front-brand__dot"></span>
    <span class="front-brand__name">Marlow Estate<br>Fixers</span>
  </div>

  <span class="divider"></span>

  <div class="person">
    <h1 class="person__name"><strong>Petra</strong> Novak</h1>
    <p class="person__title">Founder &amp; CEO</p>
  </div>

  <ul class="contact-list">
    <li>
      <svg viewBox="0 0 16 16" aria-hidden="true"><rect x="4" y="1" width="8" height="14" rx="1.5" fill="none" stroke="#ec2a2f" stroke-width="1.4"/><circle cx="8" cy="12.5" r=".9" fill="#ec2a2f"/></svg>
      (555) 214-3087
    </li>
    <li>
      <svg viewBox="0 0 16 16" aria-hidden="true"><path d="M3 2.5l2.4-.5 1.3 3-1.5 1.1a8 8 0 0 0 4.7 4.7l1.1-1.5 3 1.3-.5 2.4C8 13.5 2.5 8 3 2.5z" fill="#ec2a2f"/><path d="M10 2.5a4 4 0 0 1 3.5 3.5M10 .8a5.8 5.8 0 0 1 5.2 5.2" fill="none" stroke="#ec2a2f" stroke-width="1.1"/></svg>
      (555) 310-4422
    </li>
    <li>
      <svg viewBox="0 0 16 16" aria-hidden="true"><circle cx="8" cy="8" r="6.8" fill="none" stroke="#ec2a2f" stroke-width="1.3"/><path d="M1.2 8h13.6M8 1.2c-2.5 2-2.5 11.6 0 13.6M8 1.2c2.5 2 2.5 11.6 0 13.6" fill="none" stroke="#ec2a2f" stroke-width="1.1"/></svg>
      <span>www.<span class="accent">marlowfixers</span>.com</span>
    </li>
    <li>
      <svg viewBox="0 0 16 16" aria-hidden="true"><rect x="1" y="4" width="14" height="10" fill="none" stroke="#ec2a2f" stroke-width="1.3"/><path d="M1 4l7 5.5L15 4" fill="none" stroke="#ec2a2f" stroke-width="1.3"/></svg>
      <span>info@<span class="accent">marlowfixers</span>.com</span>
    </li>
  </ul>

  <p class="address">418 Harlow Ave Dalton, Texas 75090 USA</p>
</section>

</body>
</html>
```